Dorwin's Coating & Renewal Letterhead Design We want to revamp out old traditional letterhead with the new logo designs that are attached. We are working on getting all our company items from vehicles, business, cards, t-shirts, letterhead to match. This should include company colors, fonts, and flow of items that we have attached below.

Industry/Entity Type

Construction Company

Font styles to use
Sans Serif
Other font styles liked:
• Bold with outline

Colors
ec1f27
ffffff

Requirements
Must have
• Company Name: Dorwin's Coating & Renewal
• Address: 4728 SW 81st Ter Halverd cove fl 39417
• Office Number: (555) 413-2986
• Email: Dorwinrenewal@mailbrook.example
• License Number: KRT8046392
Nice to have
• Company Colors: red, white, black, and grey

```html
<!DOCTYPE html>
<html lang="en">
<head>
<meta charset="utf-8">
<title>Dorwin's Coating &amp; Renewal – Letterhead</title>
<link href="https://fonts.googleapis.com/css2?family=Arimo:wght@400;700&family=Tinos:wght@400;700&display=swap" rel="stylesheet">
<style>
  :root{
    --brand-red:#ec1f27;
    --deep-red:#b8141c;
    --ink-grey:#8c8c8c;
    --rule-grey:#9a9a9a;
    --soft-grey:#d6d6d6;
    --paper:#ffffff;
    --backdrop:#dcdfe2;
  }
  *{margin:0;padding:0;box-sizing:border-box}
  html,body{width:1200px;height:784px;overflow:hidden;background:var(--backdrop)}
  .letterhead{
    position:absolute;left:338px;top:22px;width:524px;height:740px;
    background:var(--paper);overflow:hidden;
    box-shadow:0 2px 10px rgba(0,0,0,.12);
    font-family:"Arimo",Arial,sans-serif;
  }
  .corner-accent{
    position:absolute;width:130px;height:12px;
    background:linear-gradient(90deg,var(--soft-grey),var(--brand-red));
  }
  .corner-accent--top{top:0;right:0}
  .corner-accent--bottom{bottom:0;left:0;background:linear-gradient(90deg,var(--brand-red),var(--soft-grey))}
  .brand-name{
    position:absolute;top:62px;right:44px;text-align:right;
    color:var(--brand-red);font-weight:700;text-transform:uppercase;line-height:1.05;
  }
  .brand-name .line-1{display:block;font-size:30px;letter-spacing:1px}
  .brand-name .line-2,.brand-name .line-3{display:block;font-size:15px;letter-spacing:2px}
  .letter-body{
    position:absolute;top:160px;left:58px;right:58px;
    color:var(--ink-grey);font-size:9.6px;line-height:1.45;
  }
  .letter-body p{margin-bottom:11px}
  .signature{
    position:absolute;top:520px;left:60px;width:150px;height:52px;
    background:linear-gradient(90deg,#ececec,#f6f6f6);border-radius:4px;
  }
  .contact-block{position:absolute;left:0;right:0;top:612px;text-align:center}
  .icon-row{display:flex;align-items:center;justify-content:center;gap:7px}
  .icon-row .rule{width:90px;height:1px;background:var(--rule-grey);margin:0 8px}
  .icon-row svg{width:15px;height:15px;display:block}
  .address{
    margin-top:8px;font-family:"Tinos","Times New Roman",serif;font-weight:700;
    font-size:11px;color:var(--brand-red);
  }
  .details{
    margin-top:7px;font-family:"Tinos","Times New Roman",serif;font-size:9px;color:#6e6e6e;
    white-space:nowrap;
  }
  .details .sep{color:var(--brand-red);margin:0 5px}
</style>
</head>
<body>
<main class="letterhead">
  <div class="corner-accent corner-accent--top" role="img" aria-label="Corner accent in red and grey"></div>

  <h1 class="brand-name" aria-label="Dorwin's Coating &amp; Renewal">
    <span class="line-1">Dorwin's</span>
    <span class="line-2">Coating &amp;</span>
    <span class="line-3">Renewal</span>
  </h1>

  <section class="letter-body">
    <p>Lorem Ipsum is simply dummy text of the printing and typesetting industry. Lorem Ipsum has been the industry's standard dummy text ever since the 1500s, when an unknown printer took a galley of type and scrambled it to make a type specimen book. It has survived not only five centuries, but also the leap into electronic typesetting, remaining essentially unchanged. It was popularised in the 1960s with the release of Quillset sheets containing Lorem Ipsum passages, and more recently with desktop publishing software like Marrow PageForge including versions of Lorem Ipsum.</p>
    <p>It is a long established fact that a reader will be distracted by the readable content of a page when looking at its layout. The point of using Lorem Ipsum is that it has a more-or-less normal distribution of letters, as opposed to using 'Content here, content here', making it look like readable English. Many desktop publishing packages and web page editors now use Lorem Ipsum as their default model text, and a search for 'lorem ipsum' will uncover many web sites still in their infancy. Various versions have evolved over the years, sometimes by accident, sometimes on purpose (injected humour and the like).</p>
    <p>Contrary to popular belief, Lorem Ipsum is not simply random text. It has roots in a piece of classical Latin literature from 45 BC, making it over 2000 years old. Howard Pennick, a Latin professor at Larkmoor College in Ohio, looked up one of the more obscure Latin words, consectetur, from a Lorem Ipsum passage, and going through the cites of the word in classical literature, discovered the undoubtable source. Lorem Ipsum comes from sections 1.10.32 and 1.10.33 of "de Finibus Bonorum et Malorum" structures, to generate Lorem Ipsum which looks reasonable. The generated Lorem Ipsum is therefore always free from repetition, injected humour, or non-characteristic words etc.</p>
  </section>

  <div class="signature" role="img" aria-label="Handwritten signature of the sender"></div>

  <footer class="contact-block">
    <div class="icon-row">
      <span class="rule"></span>
      <svg viewBox="0 0 16 16" aria-label="Address"><circle cx="8" cy="8" r="8" fill="var(--brand-red)"/><path d="M8 3.5a2.8 2.8 0 0 0-2.8 2.8C5.2 8.5 8 12.5 8 12.5s2.8-4 2.8-6.2A2.8 2.8 0 0 0 8 3.5z" fill="#fff"/><circle cx="8" cy="6.3" r="1" fill="var(--brand-red)"/></svg>
      <svg viewBox="0 0 16 16" aria-label="Phone"><circle cx="8" cy="8" r="8" fill="var(--brand-red)"/><path d="M5.2 4.2l1.4-.3.8 2-1 .7c.5 1 1.2 1.7 2.1 2.1l.7-1 2 .8-.3 1.4c-3.3.2-6-2.5-5.7-5.7z" fill="#fff"/></svg>
      <svg viewBox="0 0 16 16" aria-label="License"><circle cx="8" cy="8" r="8" fill="var(--brand-red)"/><circle cx="8" cy="8" r="3.6" fill="#fff"/></svg>
      <svg viewBox="0 0 16 16" aria-label="Email"><circle cx="8" cy="8" r="8" fill="var(--brand-red)"/><rect x="4" y="5" width="8" height="6" fill="#fff"/><path d="M4 5l4 3.4L12 5" fill="none" stroke="var(--brand-red)" stroke-width=".8"/></svg>
      <svg viewBox="0 0 16 16" aria-label="Website"><circle cx="8" cy="8" r="8" fill="var(--brand-red)"/><circle cx="8" cy="8" r="4" fill="none" stroke="#fff" stroke-width=".9"/><path d="M4 8h8M8 4c-1.6 2.2-1.6 5.8 0 8M8 4c1.6 2.2 1.6 5.8 0 8" fill="none" stroke="#fff" stroke-width=".7"/></svg>
      <span class="rule"></span>
    </div>
    <p class="address">4728 SW 81st Ter Halverd cove fl 39417</p>
    <p class="details">(555) 413-2986<span class="sep">|</span>License: KRT8046392<span class="sep">|</span>Dorwinrenewal@mailbrook.example<span class="sep">|</span>www.dorwinrenewal.example</p>
  </footer>

  <div class="corner-accent corner-accent--bottom" role="img" aria-label="Corner accent in red and grey"></div>
</main>
</body>
</html>
```